Business Card Design for Vintage Jazz

I am a vintage jazz band leader in New York City. My groups play the music of the 1920s, 1930s and 1940s. My website is morvalquist.com for more info on what I do.

I am looking for a two sided business card design that has the look and feel of a really nice business card from the 1930s. I need to convey with the design that my work has that vintage kind of class and style, but also conveys that we are fun and entertaining.

Most importantly it should make a bold staement. If Hal Denbrook had a card, what would it have looked like? I want a card that I feel confident will make an impact and will let people know that my work is te the top that NYC has to offer in vintage jazz..

Note that I have only decided to avoid the "committed payment" option as I have not used this service before. Assuming that I get quality work I will select a design from those presented.

Target Market(s)

people who want to hire my band for events, media, and new fans of the band

Industry/Entity Type

Performing Art

Contact Information for Business Card

Definitely a matte finish, possibly a sort of old style of paper with that brown tint? definitely a thick card.

Requirements
Must have
• FRONT
• My name: Tobin Vashley
• What I do: Bandleader, Guitarist, Vocalist, Songwriter
• Contact Details: morvalquist.com tobin@morvalquist.com 646-555-0148
• BACK
• My Social Media Links:
• facebook.morvalquist.com
• twitter, instagram, linkedin: morvalquist
• I'm also including a photo image I would like to use. The photo's background is not needed, and to be honest isn't really desireable. Just looking to use the image of me.
Nice to have
• I'm attaching which could be used as is, omitted from the card, or altered maybe with text going around the outside of the circle or in some other way. It may need some clean up to the edges of the lettering as we only use it for the website thumbnail.
• If there's space I'd like to include the text "join our mailing list for a free song download: freesong.morvalquist.com" If not perhaps just "Download a Free Song at: freesong.morvalquist.com - something to this end.
Should not have
• anything cartoony. Don't think retro 90s's vision of the swing era, think actual swing era!
• anything modern. Got to look old school
• Try to avoid dark backgrounds. Since we often play in bars and clubs where it is dar, a d
• avoid script fonts.

```html
<!DOCTYPE html>
<html lang="en">
<head>
<meta charset="utf-8">
<title>Tobin Vashley – Business Card</title>
<link href="https://fonts.googleapis.com/css2?family=Open+Sans:wght@400;600;700&display=swap" rel="stylesheet">
<style>
  :root {
    --stage: #e4e1dc;
    --card: #efe5d2;
    --card-edge: #d8caae;
    --ink: #1e1913;
    --ink-soft: #3d342a;
    --rule: #9c8b70;
    --photo-light: #cfc3ad;
    --photo-dark: #6e6252;
  }
  * { margin: 0; padding: 0; box-sizing: border-box; }
  html, body {
    width: 1200px; height: 814px; overflow: hidden;
    background: var(--stage);
    font-family: "Open Sans", Arial, sans-serif;
    color: var(--ink);
  }
  .stage { position: relative; width: 1200px; height: 814px; }
  .card {
    position: absolute; top: 264px;
    width: 500px; height: 286px;
    background: var(--card);
    border: 1px solid var(--card-edge);
    border-radius: 3px;
    box-shadow: 0 6px 18px rgba(60,45,25,.18);
    overflow: hidden;
  }
  .card--front { left: 70px; }
  .card--back { left: 630px; }

  /* brand mark */
  .brand { display: flex; align-items: center; gap: 10px; }
  .brand__dot { width: 56px; height: 56px; border-radius: 50%; background: var(--ink); flex: none; }
  .brand__name { font-weight: 600; font-size: 15px; letter-spacing: .5px; color: var(--ink); }

  /* front */
  .card--front .brand { position: absolute; left: 28px; top: 34px; }
  .identity { position: absolute; left: 28px; top: 130px; }
  .identity__name { font-weight: 700; font-size: 17px; line-height: 1.2; }
  .identity__role { font-size: 13.5px; line-height: 1.3; color: var(--ink-soft); margin-top: 2px; }
  .contacts { list-style: none; margin-top: 10px; }
  .contacts li { display: flex; align-items: center; gap: 8px; font-size: 13.5px; line-height: 1.45; color: var(--ink-soft); }
  .contacts svg { width: 13px; height: 13px; flex: none; }
  .portrait {
    position: absolute; left: 232px; top: 36px; width: 200px; height: 250px;
    background: radial-gradient(ellipse at 45% 40%, var(--photo-light), var(--photo-dark) 80%);
    border-radius: 40px 40px 0 0;
  }

  /* back */
  .card--back .brand { position: absolute; left: 56px; top: 72px; flex-direction: column; gap: 8px; }
  .card--back .brand__dot { width: 80px; height: 80px; }
  .divider { position: absolute; left: 210px; top: 40px; width: 1px; height: 120px; background: var(--rule); }
  .social { position: absolute; left: 230px; top: 48px; list-style: none; }
  .social li { display: flex; align-items: center; gap: 8px; font-size: 12.5px; line-height: 1.75; color: var(--ink-soft); }
  .social svg { width: 13px; height: 13px; flex: none; }
  .freesong { position: absolute; right: 28px; bottom: 36px; font-size: 12.5px; color: var(--ink-soft); }
  .freesong strong { color: var(--ink); font-weight: 700; }
</style>
</head>
<body>
<main class="stage">
  <section class="card card--front">
    <div class="brand"><span class="brand__dot"></span><span class="brand__name">Morvalquist</span></div>
    <div class="identity">
      <h1 class="identity__name">Tobin Vashley</h1>
      <p class="identity__role">Bandleader, Guitarist<br>Vocalist, Songwriter</p>
      <ul class="contacts">
        <li><svg viewBox="0 0 13 13"><rect x="3" y="0.5" width="7" height="12" rx="1.2" fill="none" stroke="#1e1913" stroke-width="1.2"/><circle cx="6.5" cy="10.4" r=".8" fill="#1e1913"/></svg>646-555-0148</li>
        <li><svg viewBox="0 0 13 13"><rect x="0.5" y="2.5" width="12" height="8" fill="#1e1913"/><path d="M0.5 2.5 L6.5 7 L12.5 2.5" fill="none" stroke="#efe5d2" stroke-width="1"/></svg>tobin@morvalquist.com</li>
        <li><svg viewBox="0 0 13 13"><circle cx="6.5" cy="6.5" r="6" fill="#1e1913"/><ellipse cx="6.5" cy="6.5" rx="2.5" ry="6" fill="none" stroke="#efe5d2" stroke-width=".9"/><line x1=".5" y1="6.5" x2="12.5" y2="6.5" stroke="#efe5d2" stroke-width=".9"/></svg>morvalquist.com</li>
      </ul>
    </div>
    <div class="portrait" role="img" aria-label="Cut-out photo of the bandleader in a striped blazer tipping a boater hat"></div>
  </section>

  <section class="card card--back">
    <div class="brand"><span class="brand__dot"></span><span class="brand__name">Morvalquist</span></div>
    <span class="divider"></span>
    <ul class="social">
      <li><svg viewBox="0 0 13 13"><circle cx="6.5" cy="6.5" r="6" fill="#1e1913"/><ellipse cx="6.5" cy="6.5" rx="2.3" ry="4.6" fill="none" stroke="#efe5d2" stroke-width=".9"/><line x1="1.9" y1="6.5" x2="11.1" y2="6.5" stroke="#efe5d2" stroke-width=".9"/></svg>morvalquist.com</li>
      <li><svg viewBox="0 0 13 13"><circle cx="6.5" cy="6.5" r="6" fill="#1e1913"/><path d="M3.5 4h6v4H6L4.5 9.5V8h-1z" fill="#efe5d2"/></svg>morvalquist</li>
      <li><svg viewBox="0 0 13 13"><circle cx="6.5" cy="6.5" r="6" fill="#1e1913"/><rect x="3.5" y="5" width="6" height="4" fill="#efe5d2"/><rect x="5.2" y="3.6" width="2.6" height="1.6" fill="none" stroke="#efe5d2" stroke-width=".8"/></svg>morvalquist</li>
      <li><svg viewBox="0 0 13 13"><circle cx="6.5" cy="6.5" r="6" fill="#1e1913"/><path d="M5.6 7.4l1.8-1.8M4.8 6.2l-1 1a1.3 1.3 0 0 0 1.9 1.9l1-1M8.2 6.8l1-1a1.3 1.3 0 0 0-1.9-1.9l-1 1" fill="none" stroke="#efe5d2" stroke-width=".9" stroke-linecap="round"/></svg>morvalquist</li>
    </ul>
    <p class="freesong">Download a Free Song at: <strong>freesong.morvalquist.com</strong></p>
  </section>
</main>
</body>
</html>
```